Heron Home Inspections website

I need a website for a new company called Heron Home Inspections, LLC. based in Northern Virginia. I'd like the site built on the url heroninspections.example and incorporating the graphics that I attached.
Updates

Project Deadline Extended
Reason: I got bogged down with my job, with a daughter moving, and with two daughters who are in their final stages of pregnancy. I started this web design job at a really bad time in my life. I do appreciate all of the hard work that the designers have put forth and I will soon make my selection. Thank you, Tom

Target Market(s)

Clarke County, Loudoun County, Fairfax County, Fairfax City, Fauquier County, Arlington County, Arlington City, Frederick County, Shenandoah County

Industry/Entity Type

Home Inspection

Number of Pages Required

1 page

Font styles to use
Sans Serif

Requirements
Must have
• My logo
• Company name: Heron Home Inspections, LLC.
• Tom Keller, Jr.
• Owner / Principal Inspector
• 555-418-2973
• tom.heroninspections@mailbox.example
• A space to describe me and my business
Should not have
• Please use the color scheme of the uploads that I provided

```html
<!DOCTYPE html>
<html lang="en">
<head>
<meta charset="utf-8">
<title>Heron Home Inspections, LLC</title>
<link href="https://fonts.googleapis.com/css2?family=Raleway:wght@400;500;600&family=Open+Sans:wght@400;600&display=swap" rel="stylesheet">
<style>
:root{
  --blue:#2a8fd6;
  --blue-light:#4ab0ea;
  --navy:#1f4a8c;
  --footer-top:#4a76c2;
  --footer-bottom:#2650a6;
  --ink:#222;
  --body:#555;
  --rule:#d8d8d8;
  --photo-warm:#d9b48a;
  --photo-warm-dark:#b8875a;
}
*{box-sizing:border-box;margin:0;padding:0}
html,body{width:1154px;height:1200px;overflow:hidden}
body{position:relative;background:#fff;font-family:'Open Sans',Arial,sans-serif;color:var(--body)}
.site-header{position:absolute;left:0;top:0;width:1154px;height:162px;background:linear-gradient(#fff,#ededed);border-bottom:1px solid #d6d6d6}
.logo{position:absolute;left:191px;top:12px;width:144px;height:95px;background:#fff;display:flex;flex-direction:column;align-items:center;justify-content:center;gap:8px;padding:6px}
.logo-mark{width:26px;height:26px;background:var(--blue)}
.logo-name{font-family:'Raleway',sans-serif;font-weight:600;font-size:13px;line-height:1.2;color:var(--navy);text-align:center}
.call{position:absolute;right:188px;top:52px;text-align:right;font-family:'Raleway',sans-serif}
.call-label{font-size:15px;color:var(--blue)}
.call-number{font-size:19px;color:var(--ink);display:flex;align-items:center;justify-content:flex-end;gap:6px;margin-top:2px}
.call-email{font-family:'Open Sans',sans-serif;font-size:10px;color:var(--body);margin-top:2px}
.main-nav{position:absolute;left:184px;top:117px;width:787px;height:43px;background:linear-gradient(var(--blue-light),var(--blue));display:flex;font-family:'Raleway',sans-serif;font-weight:600;font-size:15px;color:#fff}
.main-nav a{display:flex;align-items:center;justify-content:center;border-right:1px solid rgba(255,255,255,.35);color:#fff;text-decoration:none}
.main-nav a:last-child{border-right:none}
.hero{position:absolute;left:184px;top:162px;width:787px;height:354px;border-radius:0 0 4px 4px;background:linear-gradient(90deg,var(--photo-warm) 0%,#c9a27a 35%,#8fa6c8 60%,var(--photo-warm) 100%)}
.hero-caption{position:absolute;left:190px;top:102px;width:412px;height:126px;background:rgba(30,30,30,.85);text-align:center;color:#fff;font-family:'Raleway',sans-serif;padding-top:20px}
.hero-caption h1{font-weight:500;font-size:24px;letter-spacing:.3px}
.hero-caption h2{font-weight:500;font-size:14px;margin-top:6px}
.hero-caption p{font-family:'Open Sans',sans-serif;font-size:10px;line-height:15px;color:#ddd;margin:12px auto 0;width:320px}
.hero-dots{position:absolute;left:365px;top:336px;display:flex;gap:4px}
.hero-dots span{width:11px;height:11px;border-radius:50%;background:#222}
.about{position:absolute;left:187px;top:556px;width:520px}
.about h2{font-family:'Raleway',sans-serif;font-weight:400;font-size:24px;color:var(--ink)}
.about .lead{font-size:11px;line-height:20px;color:#333;margin-top:8px}
.about .more{font-size:9.5px;line-height:17px;margin-top:6px}
.badge-round{position:absolute;left:733px;top:573px;width:96px;height:96px;border-radius:50%;background:#111}
.badge-chapter{position:absolute;left:852px;top:596px;width:118px;height:52px;border-radius:26px 6px 6px 26px;background:#4b4a8c}
.divider{position:absolute;left:189px;top:719px;width:780px;height:1px;background:var(--rule)}
.card{position:absolute;top:757px;width:251px}
.card-photo{height:126px;background:linear-gradient(135deg,var(--photo-warm),var(--photo-warm-dark))}
.card h3{font-family:'Raleway',sans-serif;font-weight:500;font-size:19px;color:var(--blue);margin:12px 0 0 2px;white-space:nowrap}
.card p{font-size:9.5px;line-height:16.5px;margin:8px 0 0 6px;width:240px}
.btn{display:inline-block;margin:14px 0 0 5px;width:84px;height:25px;border-radius:3px;background:linear-gradient(#3a69ad,var(--navy));color:#fff;font-family:'Raleway',sans-serif;font-weight:600;font-size:10px;line-height:25px;text-align:center}
.site-footer{position:absolute;left:0;top:1090px;width:1154px;height:110px;background:linear-gradient(var(--footer-top),var(--footer-bottom))}
.footer-links{position:absolute;left:191px;top:26px;font-family:'Raleway',sans-serif;font-size:13px;color:#fff}
.footer-links span{margin:0 7px}
.copyright{position:absolute;left:191px;top:50px;font-size:10.5px;color:#e3e9f5}
.social{position:absolute;left:905px;top:38px;display:flex;gap:4px}
.social span{width:16px;height:16px;border-radius:3px;background:#fff}
</style>
</head>
<body>
<header class="site-header">
  <div class="logo"><span class="logo-mark"></span><span class="logo-name">Heron Home Inspections, LLC</span></div>
  <div class="call">
    <div class="call-label">Call Us Now</div>
    <div class="call-number">
      <svg width="15" height="15" viewBox="0 0 24 24"><path fill="#2a8fd6" d="M6.6 10.8a15 15 0 0 0 6.6 6.6l2.2-2.2c.3-.3.7-.4 1-.2 1.1.4 2.3.6 3.6.6.6 0 1 .4 1 1V20c0 .6-.4 1-1 1C10.6 21 3 13.4 3 4c0-.6.4-1 1-1h3.5c.6 0 1 .4 1 1 0 1.3.2 2.5.6 3.6.1.3 0 .7-.2 1z"/></svg>
      555.418.2973
    </div>
    <div class="call-email">tom.heroninspections@mailbox.example</div>
  </div>
  <nav class="main-nav">
    <a style="width:110px">HOME</a>
    <a style="width:123px">ABOUT US</a>
    <a style="width:186px">HOME INSPECTION</a>
    <a style="width:116px">SERVICES</a>
    <a style="width:118px">SUPPORT</a>
    <a style="width:134px">CONTACT</a>
  </nav>
</header>

<section class="hero" role="img" aria-label="Two inspectors in work clothes checking the siding of a house with a clipboard">
  <div class="hero-caption">
    <h1>HOME INSPECTION SERVICES</h1>
    <h2>ATIAM NUNC VENENATIS IN TRISTIQUE</h2>
    <p>Morbi diam mauris viverra in gravida eu mattis in ante Morbi eget arcu Morbi porta libero id ullamcorper</p>
  </div>
  <div class="hero-dots"><span></span><span></span><span></span><span></span></div>
</section>

<section class="about">
  <h2>About Heron Home Inspections, LLC</h2>
  <p class="lead">Owner / Principal Inspector, Tom Keller, Jr. is a trained builder with experience in new construction, as well as remodeling, HVAC systems, framing, roofing, siding, and masonry.</p>
  <p class="more">Maecenas aliquet velit vel turpis Mauris neque metus malesuada nec ultricies sit amet porttitor mattis enim In massa libero interdum nec interdum vel blandit sed nulla In ullamcorper est eget tempor cursus neque mi consectetuer mi a ultricies massa est sed nisl Class aptent taciti sociosqu ad litora torquent per conubi</p>
</section>
<div class="badge-round" role="img" aria-label="Professional membership badge"></div>
<div class="badge-chapter" role="img" aria-label="Regional chapter membership badge"></div>
<div class="divider"></div>

<article class="card" style="left:184px">
  <div class="card-photo" role="img" aria-label="Inspector examining a window frame on house siding"></div>
  <h3>Why get a Home Inspection</h3>
  <p>For most families, a home purchase is the largest investment that they will make in a lifetime. The decision to purchase a home should be based on a thorough review of its systems and overall condition</p>
  <span class="btn">READ MORE</span>
</article>
<article class="card" style="left:452px">
  <div class="card-photo" role="img" aria-label="Inspector explaining findings to a young couple at their home"></div>
  <h3>Why get a Home Inspection</h3>
  <p>I am a 20 year Navy veteran trained and devoted to being thorough in my inspection procedures and comprehensive in my documentation. Whether you are buying your forever home or one that you plan</p>
  <span class="btn">READ MORE</span>
</article>
<article class="card" style="left:720px">
  <div class="card-photo" role="img" aria-label="Smiling inspector holding a clipboard indoors"></div>
  <h3>Services Provide</h3>
  <p>I am a 20 year Navy veteran trained and devoted to being thorough in my inspection procedures and comprehensive in my documentation. Whether you are buying your forever home or one that you plan</p>
  <span class="btn">READ MORE</span>
</article>

<footer class="site-footer">
  <div class="footer-links">Home<span>|</span>About Us<span>|</span>Services<span>|</span>Projects<span>|</span>Support<span>|</span>Contact</div>
  <div class="copyright">© 2015 Company Name &nbsp;All right reserved &nbsp;Term of Use</div>
  <div class="social"><span></span><span></span><span></span></div>
</footer>
</body>
</html>
```